Recto Verso Audiology Business Card

Business card with a beautiful design on the back. On the Recto you need the following data Lindqvist Oren Audiologist Hearing Solutions Hearing Protection Tinnitus Hyperacusis Tel: 0482/37 59 08 Email: On the back, you need something nice like the attached file. The logo "Corra Luna" can be in the center The colors of the Logo can not be changed If possible stay in the same colors as the logo Another solution is to put the logo on the front and have a nice back (A mosaic of small ears, hearing aids or other ..) Thank you _______________________________________________________________ Visit card On the Recto Lindqvist Oren Audiologist Hearing Solutions Hearing Protection Tinnitus Hyperacusis Tel: 0482/37 59 08 Email: You can put the logo " Corra Luna "on the Recto of the Verso The colors of the logo can not be changed. If you put the logo on the back, it must be well integrated. On the Verso I need something in the files. something stylish. It's a visit card for an audiologist. You can get ears of hearing aids if you need. Thanks

Target Market(s)

customers

Contact Information for Business Card

Carte de visite standard ou A6

Font styles to use
Serif
Sans Serif

Colors
33a6d7

Requirements
Must have
• the logo and a stylized background.
Nice to have
• It would be nice to have a back side related to audiology (ears, hearing aids etc.)

```html
<!DOCTYPE html>
<html lang="en">
<head>
<meta charset="utf-8">
<title>Corra Luna – Audiology Business Card</title>
<link rel="stylesheet" href="https://fonts.googleapis.com/css2?family=Barlow:wght@400;500&display=swap">
<style>
  :root {
    --teal: #3aaebf;
    --ink: #3a3f44;
    --paper: #fbfbfa;
    --pattern-light: #f4f4f3;
    --pattern-mid: #e4e4e3;
    --pattern-dark: #d6d6d5;
    --backdrop: #e9e6e1;
    --shadow: rgba(60, 50, 40, 0.18);
  }
  * { box-sizing: border-box; margin: 0; padding: 0; }
  html, body {
    width: 1200px;
    height: 870px;
    overflow: hidden;
    background: var(--backdrop);
    font-family: "Barlow", Arial, sans-serif;
  }
  .stage {
    position: relative;
    width: 1200px;
    height: 870px;
  }
  .card {
    position: absolute;
    width: 560px;
    height: 340px;
    background: var(--paper);
    box-shadow: 0 6px 18px var(--shadow);
    overflow: hidden;
  }

  /* Back side */
  .card--back { left: 90px; top: 80px; }
  .back-pattern {
    position: absolute;
    inset: 0;
    background:
      radial-gradient(ellipse at 50% 50%, var(--pattern-light) 0%, rgba(244,244,243,0) 60%),
      linear-gradient(150deg, var(--pattern-mid) 0%, var(--pattern-dark) 50%, var(--pattern-mid) 100%);
  }
  .back-brand {
    position: absolute;
    left: 50%;
    top: 50%;
    transform: translate(-50%, -50%);
    background: var(--paper);
    padding: 20px 28px;
    color: var(--teal);
    font-weight: 500;
    font-size: 32px;
    line-height: 1.1;
    letter-spacing: 1px;
    text-transform: uppercase;
    white-space: nowrap;
  }

  /* Front side */
  .card--front { left: 550px; top: 450px; }
  .front-brand {
    position: absolute;
    left: 40px;
    top: 118px;
    color: var(--teal);
    font-weight: 500;
    font-size: 26px;
    line-height: 1.1;
    letter-spacing: 1px;
    text-transform: uppercase;
    white-space: nowrap;
  }
  .contact {
    position: absolute;
    left: 270px;
    top: 88px;
    color: var(--ink);
  }
  .contact__name {
    color: var(--teal);
    font-weight: 500;
    font-size: 22px;
    line-height: 1.1;
    letter-spacing: 1px;
    text-transform: uppercase;
  }
  .contact__role {
    font-size: 15px;
    letter-spacing: 1px;
    text-transform: uppercase;
    margin: 4px 0 18px;
  }
  .contact__line {
    font-size: 14px;
    line-height: 1.45;
  }
  .services-band {
    position: absolute;
    left: 0;
    right: 0;
    bottom: 0;
    height: 40px;
    background: var(--teal);
    color: #fff;
    font-size: 15px;
    letter-spacing: 0.5px;
    display: flex;
    align-items: center;
    padding-left: 40px;
    white-space: nowrap;
  }
</style>
</head>
<body>
  <main class="stage">
    <section class="card card--back" aria-label="Business card back">
      <div class="back-pattern" role="img" aria-label="Allover repeating pattern of small line-drawn ears and hearing aids in light grey on white"></div>
      <div class="back-brand">Corra Luna</div>
    </section>

    <section class="card card--front" aria-label="Business card front">
      <div class="front-brand">Corra Luna</div>
      <div class="contact">
        <p class="contact__name">Lindqvist Oren</p>
        <p class="contact__role">Audiologist Hearing</p>
        <p class="contact__line">P. 0482/37 59 08</p>
        <p class="contact__line">info@medicalcentercorraluna.com</p>
        <p class="contact__line">www.medicalcentercorraluna.com</p>
      </div>
      <div class="services-band">Solutions Hearing | Protection | Tinnitus | Hyperacusis</div>
    </section>
  </main>
</body>
</html>
```